Website homepage rework for women's travel website

I have a homepage (http://www.ladies-at-the-helm.com) that I'm 50% happy with but don't want to completely overhaul. I'd like to retain a similar look but upgrade it to something a bit more modern and less old-fashioned. The basic sense of the site is empowering, self-confident, fun and adventurous - but female and over 40.

A number of the elements on the page have to be redesigned, a few can be tweaked, and a few left alone. See the rest of the brief for further information.

Target Market(s)

women over 40 who like to travel

Industry/Entity Type

Travel

Number of Pages Required

1 page

Font styles to use
Other font styles liked:
• see my brief

Requirements
Must have
• - size - the page must be significantly wider
• - the only font I MUST keep is Raleway (as in the tagline) and possibly the font of the site name (Ladies at the Helm). Both of those work for me. There are too many fonts on the page, however, and that needs to be unified.
• - the rectangles I click to get inside the site have to change to something more modern, possibly square - they do not have to be separated into two columns as they are now, nor do they need the titles (toolkit etc)
• - I like the background image of the header - but it needs to be wider of course - also keep in mind the aspect - it has to fit into the smaller inside pages, whose size will not change
• - at the end of the project I need to receive the separate elements of the design so I can eventually make a change myself if needed ie. replace my own photo, for example
Nice to have
• - the three photos need to change to something more eye-popping - or something else should take their place to fill the space
Should not have
• I do not want a full, original redesign. I want my readers to still feel as though they are on the same site - same header, mostly same fonts.

```html
<!DOCTYPE html>
<html lang="en">
<head>
<meta charset="utf-8">
<title>Ladies at the Helm – Home</title>
<link rel="stylesheet" href="https://fonts.googleapis.com/css2?family=Open+Sans:wght@400;600;700&family=Raleway:wght@400&family=Roboto+Condensed:wght@400;700&display=swap">
<style>
  :root {
    --canvas: #000000;
    --nav: #2f2f30;
    --band: #2e2d2f;
    --white: #ffffff;
    --ink: #2b2b2b;
    --accent: #d8400d;
    --link: #ffd21a;
    --brand-box: #e8590c;
    --tile-red: #cc1f0f;
    --tile-orange: #e4700c;
    --tile-blue: #1456a5;
    --tile-green: #0ccf24;
    --dest-sky: #3ab3f2;
    --dest-red: #cb1010;
    --dest-teal: #3fdccb;
    --dest-yellow: #efd31a;
    --divider: #e2e2e2;
  }
  * { box-sizing: border-box; margin: 0; padding: 0; }
  html, body { width: 850px; height: 1200px; overflow: hidden; background: var(--canvas); }
  body { font-family: "Open Sans", sans-serif; color: var(--ink); }
  .page { position: relative; width: 850px; height: 1200px; }
  .abs { position: absolute; }

  /* navigation */
  .main-nav { left: 42px; top: 21px; width: 765px; height: 40px; background: var(--nav); }
  .main-nav a { position: absolute; top: 14px; transform: translateX(-50%); color: var(--white);
    font-size: 10px; font-weight: 700; text-decoration: none; white-space: nowrap; letter-spacing: .2px; }

  /* header */
  .hero { left: 42px; top: 61px; width: 765px; height: 288px; overflow: hidden; }
  .hero-photo { width: 100%; height: 100%;
    background: linear-gradient(180deg, #ee7a0c 0%, #f5a312 18%, #fbd32a 36%, #f4b23a 44%, #c2461a 52%, #a8361a 60%, #9c5a2c 72%, #7d5638 86%, #5e4a3a 100%); }
  .brand { right: 15px; top: 19px; background: var(--brand-box); padding: 3px 12px 5px;
    font-family: "Raleway", sans-serif; font-weight: 400; font-size: 32px; color: var(--white); line-height: 1.1; }
  .tagline { right: 16px; top: 63px; font-family: "Raleway", sans-serif; font-size: 16px; color: #3a2a20; }

  /* intro */
  .intro { left: 42px; top: 349px; width: 765px; height: 203px; background: var(--white); }
  .intro-title { position: absolute; left: 0; top: 42px; width: 100%; text-align: center;
    font-size: 15.5px; font-weight: 700; line-height: 22px; color: var(--ink); }
  .pillar { position: absolute; top: 113px; }
  .pillar-icon { position: absolute; left: 0; top: 0; }
  .pillar-text { position: absolute; top: 2px; font-size: 10px; line-height: 16px; color: #333; }
  .pillar-text strong { color: var(--accent); font-size: 12px; font-weight: 700; }
  .divider { position: absolute; top: 113px; width: 1px; height: 50px; background: var(--divider); }

  /* solo band */
  .solo-band { left: 42px; top: 552px; width: 765px; height: 166px; background: var(--band); }
  .solo-title { position: absolute; left: 28px; top: 41px; color: var(--white);
    font-size: 16px; font-weight: 700; line-height: 23px; }
  .solo-title a { color: var(--link); text-decoration: none; }
  .solo-text { position: absolute; left: 28px; top: 102px; width: 382px; color: #cfcfcf; font-size: 9px; line-height: 16px; }
  .snapshot { position: absolute; width: 86px; height: 94px; background: var(--white); padding: 5px 5px 18px;
    box-shadow: 0 2px 4px rgba(0,0,0,.5); }
  .snapshot div { width: 100%; height: 100%; }

  /* content grid */
  .content { left: 42px; top: 718px; width: 765px; height: 402px; background: var(--white); }
  .section-title { position: absolute; top: 51px; font-size: 18px; font-weight: 700; color: var(--ink); letter-spacing: .2px; }
  .tile { position: absolute; width: 168px; height: 132px; overflow: hidden;
    font-family: "Roboto Condensed", sans-serif; color: var(--white); }
  .tile-label { height: 52px; padding: 12px 13px 0; }
  .tile-label b { display: block; font-size: 12px; font-weight: 700; }
  .tile-label span { display: block; font-size: 12px; margin-top: 3px; }
  .tile-photo { height: 80px; }
  .dest { position: absolute; left: 401px; width: 338px; height: 59px; display: flex;
    font-family: "Roboto Condensed", sans-serif; color: var(--white); }
  .dest-label { width: 163px; padding: 15px 18px 0; }
  .dest-label b { display: block; font-size: 13px; font-weight: 700; }
  .dest-label span { display: block; font-size: 12px; margin-top: 2px; }
  .dest-photo { flex: 1; }

  /* footer */
  .site-footer { left: 0; top: 1146px; width: 850px; text-align: center; color: var(--white); font-size: 9px; }
  .footer-links span { margin: 0 8px; }
  .copyright { margin-top: 7px; }
</style>
</head>
<body>
<div class="page">

  <nav class="main-nav abs">
    <a href="#" style="left:111px">START HERE</a>
    <a href="#" style="left:216px">ABOUT</a>
    <a href="#" style="left:336px">TRAVEL RESOURCES</a>
    <a href="#" style="left:453px">BLOG</a>
    <a href="#" style="left:551px">TRAVEL SHOP</a>
    <a href="#" style="left:660px">CONTACT</a>
  </nav>

  <header class="hero abs">
    <div class="hero-photo" role="img" aria-label="Portrait of the site author in front of a desert road with red rock mesas under an orange sky, over a faded map"></div>
    <div class="brand abs">Ladies at the Helm</div>
    <div class="tagline abs">For women who travel smart, safe + solo</div>
  </header>

  <section class="intro abs">
    <h1 class="intro-title">HI, I'M MARLA. I TOOK MY FIRST SOLO TRIP AT 15. I'LL SHOW<br>YOU HOW TO TRAVEL...</h1>

    <div class="pillar" style="left:22px">
      <svg class="pillar-icon" width="46" height="48" viewBox="0 0 46 48" aria-hidden="true">
        <circle cx="23" cy="14" r="11" fill="none" stroke="var(--accent)" stroke-width="3"/>
        <path d="M18 25h10v5H18z" fill="var(--accent)"/>
        <path d="M19 12l4 5 4-5" fill="none" stroke="var(--accent)" stroke-width="2"/>
        <path d="M2 48c0-10 8-15 21-15s21 5 21 15z" fill="var(--accent)"/>
      </svg>
      <p class="pillar-text" style="left:61px;width:160px"><strong>SMART:</strong> practical tools to help you plan - and afford - the perfect trip</p>
    </div>
    <div class="divider" style="left:270px"></div>

    <div class="pillar" style="left:294px">
      <svg class="pillar-icon" width="48" height="48" viewBox="0 0 48 48" aria-hidden="true">
        <path d="M20 2L4 8v14c0 12 7 20 16 24 9-4 16-12 16-24V8z" fill="none" stroke="var(--accent)" stroke-width="4"/>
        <path d="M20 2v44" stroke="var(--accent)" stroke-width="2"/>
        <circle cx="35" cy="36" r="10" fill="var(--accent)"/>
        <path d="M30 36l4 4 6-7" fill="none" stroke="var(--white)" stroke-width="2.5"/>
      </svg>
      <p class="pillar-text" style="left:65px;width:128px"><strong>SAFE:</strong> down-to-earth advice and a ton of safety recommendation</p>
    </div>
    <div class="divider" style="left:516px"></div>

    <div class="pillar" style="left:538px">
      <svg class="pillar-icon" width="48" height="50" viewBox="0 0 48 50" aria-hidden="true">
        <path d="M4 14l20-8 20 8v30l-20-6-20 6z" fill="none" stroke="var(--accent)" stroke-width="3"/>
        <path d="M24 6v32" stroke="var(--accent)" stroke-width="2"/>
        <circle cx="34" cy="22" r="4" fill="var(--accent)"/>
        <path d="M34 26v8" stroke="var(--accent)" stroke-width="2"/>
      </svg>
      <p class="pillar-text" style="left:61px;width:160px"><strong>SOLO:</strong><br>yes, you can do it!</p>
    </div>
  </section>

  <section class="solo-band abs">
    <h2 class="solo-title">THINKING OF SOLO TRAVEL? <a href="#">CLICK HERE</a> TO<br>FIND OUT HOW.</h2>
    <p class="solo-text">Do you ever feel the urge to leave it all behind and start your life over - at least for a little while? That feeling hit me at 43 in what turned</p>

    <svg class="abs" style="left:466px;top:96px" width="280" height="50" viewBox="0 0 280 50" aria-hidden="true">
      <path d="M2 30c30 20 60-10 100 8s80-12 120 0 40-10 56-14" fill="none" stroke="#111" stroke-width="1.4" stroke-dasharray="4 3"/>
    </svg>
    <div class="snapshot" style="left:474px;top:33px;transform:rotate(-3deg)">
      <div role="img" aria-label="Palm trees on a tropical beach" style="background:linear-gradient(180deg,#4aa6ea 0%,#7cc4f0 40%,#1c6aa8 62%,#1a3a4a 100%)"></div>
    </div>
    <div class="snapshot" style="left:560px;top:38px;transform:rotate(3deg)">
      <div role="img" aria-label="Blue pots and agave against a terracotta wall" style="background:linear-gradient(160deg,#e0702e 0%,#ee9450 35%,#1f8fd6 60%,#8cc63a 100%)"></div>
    </div>
    <div class="snapshot" style="left:646px;top:32px;transform:rotate(-2deg)">
      <div role="img" aria-label="Red scooter parked in a colourful old street" style="background:linear-gradient(180deg,#e0563a 0%,#d9824c 35%,#5f9a3e 65%,#9a8e80 100%)"></div>
    </div>
  </section>

  <main class="content abs">
    <h2 class="section-title" style="left:17px">TRAVEL TOOLKIT</h2>
    <h2 class="section-title" style="left:400px">DESTINATION</h2>

    <a class="tile" style="left:17px;top:94px">
      <div class="tile-label" style="background:var(--tile-red)"><b>NO SINGLE SUPPLEMENT</b><span>17 ways to avoid paying it</span></div>
      <div class="tile-photo" role="img" aria-label="Palm tree against a clear sky" style="background:linear-gradient(180deg,#6f9bb8 0%,#b9cbd2 45%,#5f7a3a 75%,#8a6a3c 100%)"></div>
    </a>
    <a class="tile" style="left:196px;top:94px">
      <div class="tile-label" style="background:var(--tile-orange)"><b>EATING WITH LOCAL</b><span>The ultimate guide to social</span></div>
      <div class="tile-photo" role="img" aria-label="Hands sharing a plate of salad" style="background:linear-gradient(135deg,#d9d6d2 0%,#bfb6aa 40%,#4f9a2a 65%,#2f7a1e 100%)"></div>
    </a>
    <a class="tile" style="left:17px;top:240px">
      <div class="tile-label" style="background:var(--tile-blue)"><b>YOUR PACKING LIST</b><span>Take what you need - no more</span></div>
      <div class="tile-photo" role="img" aria-label="Winding mountain road seen from above" style="background:linear-gradient(180deg,#1f5fa8 0%,#4a86c0 30%,#3f6a78 55%,#7a6a52 80%,#4e4236 100%)"></div>
    </a>
    <a class="tile" style="left:196px;top:240px">
      <div class="tile-label" style="background:var(--tile-green)"><b>STRESS MANAGEMENT</b><span>How to travel stress - free</span></div>
      <div class="tile-photo" role="img" aria-label="Hand brushing through a wheat field" style="background:linear-gradient(180deg,#6f9e2a 0%,#b8b83a 40%,#dcae3a 70%,#8a6a22 100%)"></div>
    </a>

    <a class="dest" style="top:94px">
      <div class="dest-label" style="background:var(--dest-sky)"><b>SOLO IN ARGENTINA</b><span>Does it really take to tango?</span></div>
      <div class="dest-photo" role="img" aria-label="Green rolling countryside" style="background:linear-gradient(180deg,#8fb6d0 0%,#7fa45a 25%,#5c9a24 55%,#3d7218 100%)"></div>
    </a>
    <a class="dest" style="top:167px">
      <div class="dest-label" style="background:var(--dest-red)"><b>EUROPE FOR FOODIES</b><span>9 top destination</span></div>
      <div class="dest-photo" role="img" aria-label="Pan of colourful cooked vegetables on a slate table" style="background:linear-gradient(90deg,#56627a 0%,#4a5670 40%,#2a2a2a 55%,#d9a82a 72%,#2a2a2a 92%,#4a5670 100%)"></div>
    </a>
    <a class="dest" style="top:240px">
      <div class="dest-label" style="background:var(--dest-teal)"><b>SOLO FEMALE TRAVEL</b><span>A 3-week Central Asia</span></div>
      <div class="dest-photo" role="img" aria-label="Sunlit sea horizon" style="background:linear-gradient(90deg,#2f7fc8 0%,#6eb2e2 35%,#e8eef0 65%,#f6b232 90%,#e88a1a 100%)"></div>
    </a>
    <a class="dest" style="top:312px">
      <div class="dest-label" style="background:var(--dest-yellow)"><b>REBELLIOUS CAROUGE</b><span>Geneva's Alter Ego?</span></div>
      <div class="dest-photo" role="img" aria-label="Hiker on a snowy mountain summit" style="background:linear-gradient(180deg,#1a5eb8 0%,#4a8ad6 40%,#e6eef6 70%,#5f6f88 100%)"></div>
    </a>
  </main>

  <footer class="site-footer abs">
    <div class="footer-links">License information<span>|</span>Legal agreements<span>|</span>Terms of use<span>|</span>Privacy policy</div>
    <div class="copyright">Copyright © 2016, All Right Reserved.</div>
  </footer>

</div>
</body>
</html>
```